Executive Business Card for Healthcare Company [Need Today]

I need a business card design for a healthcare company. The only branding the company has thus far is a logo. The cards will be utilized by company executives. The design I envision will be vibrant and appealing but with a corporate feel. They shouldn't be too casual or playful. I would like to complete this project TODAY if possible.

Target Market(s)

Healthcare vendors, other executives in healthcare and pharmaceuticals

Industry/Entity Type

Pharmaceutical

Contact Information for Business Card

See attachment

Font styles to use
Serif
Sans Serif

Colors

Designer to choose colors to be used in the design.

```html
<!DOCTYPE html>
<html lang="en">
<head>
<meta charset="utf-8">
<title>Corvan Therapeutics — Business Card</title>
<link rel="stylesheet" href="https://fonts.googleapis.com/css2?family=Roboto:wght@300;400&display=swap">
<style>
  :root {
    --bg: #e9eaec;
    --teal: #22a9c2;
    --green: #4eb08a;
    --card-white: #f7f7f6;
    --ink: #3b3d40;
    --ink-soft: #6a6d71;
    --white: #ffffff;
  }
  * { box-sizing: border-box; margin: 0; padding: 0; }
  html, body {
    width: 1200px; height: 726px; overflow: hidden;
    background: var(--bg);
    font-family: "Roboto", Arial, sans-serif;
  }
  .stage {
    width: 1200px; height: 726px;
    display: flex; align-items: center; justify-content: center; gap: 56px;
  }
  .card {
    width: 520px; height: 297px; position: relative; overflow: hidden;
    box-shadow: 0 6px 18px rgba(0,0,0,0.12);
  }
  /* Back side */
  .card--back {
    background: linear-gradient(160deg, var(--teal) 0%, #36b3b0 50%, var(--green) 100%);
    color: var(--white);
  }
  .card--back .wordmark {
    position: absolute; left: 0; right: 0; top: 92px; text-align: center;
    font-weight: 300; font-size: 44px; letter-spacing: 1px; line-height: 1.05;
  }
  .card--back .wordmark span { display: block; font-size: 30px; letter-spacing: 2px; }
  .card--back .web {
    position: absolute; left: 0; right: 0; bottom: 36px; text-align: center;
    font-weight: 300; font-size: 13px; letter-spacing: 4px;
  }
  /* Front side */
  .card--front { background: var(--card-white); }
  .card--front .wordmark {
    position: absolute; left: 30px; top: 38px;
    color: var(--teal); font-weight: 300; font-size: 34px; line-height: 1.05;
  }
  .card--front .wordmark span { display: block; font-size: 22px; letter-spacing: 1px; }
  .ring {
    position: absolute; right: -28px; top: 26px; width: 250px; height: 250px;
    border: 5px solid var(--green); border-radius: 50%;
  }
  .edge-dot {
    position: absolute; left: -16px; top: 168px; width: 32px; height: 52px;
    background: var(--teal); border-radius: 50%;
  }
  .person { position: absolute; left: 38px; top: 140px; }
  .person .name { color: var(--teal); font-size: 20px; font-weight: 400; }
  .person .title { color: var(--ink-soft); font-size: 10px; margin-top: 3px; }
  .contact {
    position: absolute; left: 38px; top: 200px; list-style: none;
    color: var(--ink); font-size: 12.5px; font-weight: 300;
  }
  .contact li { display: flex; align-items: center; gap: 8px; height: 18px; }
  .contact svg { width: 11px; height: 11px; fill: var(--teal); flex: none; }
  .contact .accent { color: var(--teal); }
  .contact .address { margin-top: 4px; }
</style>
</head>
<body>
<main class="stage">
  <section class="card card--back" aria-label="Card back">
    <p class="wordmark">corvan<span>therapeutics</span></p>
    <p class="web">www.corvanrx.com</p>
  </section>

  <section class="card card--front" aria-label="Card front">
    <p class="wordmark">corvan<span>therapeutics</span></p>
    <div class="ring" aria-hidden="true"></div>
    <div class="edge-dot" aria-hidden="true"></div>
    <div class="person">
      <p class="name">Daniel Hale</p>
      <p class="title">Senior Director of Marketing</p>
    </div>
    <ul class="contact">
      <li>
        <svg viewBox="0 0 24 24" aria-hidden="true"><path d="M6.6 10.8a15.1 15.1 0 0 0 6.6 6.6l2.2-2.2a1 1 0 0 1 1-.25 11.4 11.4 0 0 0 3.6.57 1 1 0 0 1 1 1V20a1 1 0 0 1-1 1A17 17 0 0 1 3 4a1 1 0 0 1 1-1h3.5a1 1 0 0 1 1 1c0 1.25.2 2.45.57 3.57a1 1 0 0 1-.25 1z"/></svg>
        555-210-4837
      </li>
      <li>
        <svg viewBox="0 0 24 24" aria-hidden="true"><path d="M7 1h10a2 2 0 0 1 2 2v18a2 2 0 0 1-2 2H7a2 2 0 0 1-2-2V3a2 2 0 0 1 2-2zm0 3v14h10V4zm5 15.5a1.2 1.2 0 1 0 0 2.4 1.2 1.2 0 0 0 0-2.4z"/></svg>
        555-378-6142
      </li>
      <li>
        <svg viewBox="0 0 24 24" aria-hidden="true"><path d="M12 2a10 10 0 1 0 0 20 10 10 0 0 0 0-20zm6.9 6h-2.9a15.6 15.6 0 0 0-1.4-3.6A8 8 0 0 1 18.9 8zM12 4a14 14 0 0 1 1.9 4h-3.8A14 14 0 0 1 12 4zM4.3 14a8 8 0 0 1 0-4h3.4a16 16 0 0 0 0 4zm.8 2h2.9a15.6 15.6 0 0 0 1.4 3.6A8 8 0 0 1 5.1 16zM8 8H5.1a8 8 0 0 1 4.3-3.6A15.6 15.6 0 0 0 8 8zm4 12a14 14 0 0 1-1.9-4h3.8A14 14 0 0 1 12 20zm2.3-6H9.7a14.7 14.7 0 0 1 0-4h4.6a14.7 14.7 0 0 1 0 4zm.3 5.6A15.6 15.6 0 0 0 16 16h2.9a8 8 0 0 1-4.3 3.6zM16.3 14a16 16 0 0 0 0-4h3.4a8 8 0 0 1 0 4z"/></svg>
        dhale@<span class="accent">corvanrx.com</span>
      </li>
      <li class="address">418 W Maple Avenue Fairview, GA 30499</li>
    </ul>
  </section>
</main>
</body>
</html>
```